Wine Label Design

We are looking for a new label to add to our winery. This is to be named "Kornweil" which is the German word for schoolhouse. Our tasting room is a one room school house built in 1887. I would like the label to be very simple and clean with a schoolhouse on the front. I would like to schoolhouse to be sketch style, not a cartoonish design. I have attached a photo of the schoolhouse that we pour from, this is what I would want the schoolhouse to resemble. I have also added a copy of our current "higher end" label so that you have an idea of our style. I would like the new label to be cohesive with our old label and look good next to each other on our shelves. Just as added clarification we do not want Dunbury Vineyards on the new label - we want that replaced with Kornweil. If you are unable to do a full label design we would also accept just the schoolhouse drawing design as well. Thank you.

Logo Text

Kornweil

```html
<!DOCTYPE html>
<html lang="en">
<head>
<meta charset="utf-8">
<title>Kornweil – Wine Label</title>
<link rel="stylesheet" href="https://fonts.googleapis.com/css2?family=Raleway:wght@300;400&family=Libre+Baskerville:wght@700&display=swap">
<style>
  :root {
    --page-bg: #ffffff;
    --label-bg: #ffffff;
    --ink: #1d1d1b;
    --ink-soft: #3a3a38;
    --gold: #c9a13a;
    --gold-light: #e6c66a;
    --gold-deep: #a67c1e;
    --shadow: rgba(0, 0, 0, 0.12);
  }
  * { margin: 0; padding: 0; box-sizing: border-box; }
  html, body {
    width: 1162px;
    height: 1200px;
    overflow: hidden;
    background: var(--page-bg);
  }
  .canvas {
    position: relative;
    width: 1162px;
    height: 1200px;
  }
  .wine-label {
    position: absolute;
    left: 290px;
    top: 100px;
    width: 582px;
    height: 1000px;
    background: var(--label-bg);
    border-radius: 47px;
    box-shadow: 0 2px 14px var(--shadow);
  }
  .schoolhouse-art {
    position: absolute;
    left: 172px;
    top: 96px;
    width: 238px;
    height: 240px;
  }
  .brand-name {
    position: absolute;
    left: 0;
    right: 0;
    top: 386px;
    text-align: center;
    font-family: "Raleway", sans-serif;
    font-weight: 400;
    font-size: 60px;
    letter-spacing: 6px;
    color: var(--ink);
  }
  .vintage,
  .varietal,
  .region {
    position: absolute;
    left: 0;
    right: 0;
    text-align: center;
  }
  .vintage {
    top: 638px;
    font-family: "Raleway", sans-serif;
    font-weight: 400;
    font-size: 25px;
    letter-spacing: 1px;
    color: var(--ink-soft);
  }
  .varietal {
    top: 718px;
    font-family: "Libre Baskerville", serif;
    font-weight: 700;
    font-size: 26px;
    letter-spacing: 1px;
    color: var(--gold);
  }
  .region {
    top: 794px;
    font-family: "Raleway", sans-serif;
    font-weight: 300;
    font-size: 25px;
    letter-spacing: 2px;
    color: var(--ink);
  }
</style>
</head>
<body>
  <main class="canvas">
    <section class="wine-label">
      <svg class="schoolhouse-art" viewBox="0 0 238 240" role="img" aria-label="Gold sketch-style drawing of the one-room schoolhouse">
        <defs>
          <linearGradient id="goldTone" x1="0" y1="0" x2="1" y2="1">
            <stop offset="0" stop-color="var(--gold-light)"/>
            <stop offset="0.55" stop-color="var(--gold)"/>
            <stop offset="1" stop-color="var(--gold-deep)"/>
          </linearGradient>
        </defs>
        <rect x="0" y="0" width="238" height="240" rx="6" fill="url(#goldTone)"/>
      </svg>
      <h1 class="brand-name">KORNWEIL</h1>
      <p class="vintage">2016</p>
      <p class="varietal">GEWÜRZTRAMINER</p>
      <p class="region">FINGER LAKES</p>
    </section>
  </main>
</body>
</html>
```